OWNERS HANDBOOK

Take a MICROSOFT WORD document and turn it into a nicely designed and structured PDF or similar to circulate to Owners and to make available online for Owners to access.

```html
<!DOCTYPE html>
<html lang="en">
<head>
<meta charset="utf-8">
<title>Owners Handbook 2023 – Page Spreads</title>
<link href="https://fonts.googleapis.com/css2?family=Montserrat:wght@400;500;600;700;800&family=Oswald:wght@500;600;700&display=swap" rel="stylesheet">
<style>
  :root{
    --blue:#2f55b3;
    --blue-deep:#2846a0;
    --ink:#1d1d1f;
    --text:#3a3a3f;
    --paper:#ffffff;
    --bg:#d6d7dc;
    --band:#b6bace;
    --band-soft:#c3c6d6;
    --green:#2e9a49;
  }
  *{box-sizing:border-box;margin:0;padding:0}
  html,body{width:1172px;height:1200px;overflow:hidden;background:var(--bg);font-family:"Montserrat",sans-serif;color:var(--text)}
  .stage{position:relative;width:1172px;height:1200px;overflow:hidden}
  .backdrop{position:absolute;inset:0}
  .page{position:absolute;width:212px;height:299px;background:var(--paper);overflow:hidden;box-shadow:0 5px 4px -3px rgba(0,0,0,.25)}
  .c1{left:113px}.c2{left:358px}.c3{left:602px}.c4{left:846px}
  .r1{top:105px}.r2{top:445px}.r3{top:785px}

  .run-head{position:absolute;top:8px;left:0;right:0;height:7px}
  .run-head .tab{position:absolute;left:0;top:0;width:35px;height:7px;background:var(--ink);border-radius:0 4px 4px 0}
  .run-head .bar{position:absolute;left:39px;right:0;top:0;height:7px;background:var(--blue);border-radius:4px 0 0 4px;color:#fff;font-size:3.5px;font-weight:600;letter-spacing:.25px;text-align:right;padding-right:10px;line-height:7px}
  .run-foot{position:absolute;left:8px;right:8px;bottom:9px;height:7px;background:var(--blue);border-radius:4px;color:#fff;font-size:3.6px;font-weight:700;letter-spacing:.25px;display:flex;justify-content:space-between;align-items:center;padding:0 5px}
  .run-foot span:last-child{font-weight:500}

  .body{position:absolute;left:10px;right:11px;top:28px}
  .title{font-size:7.6px;font-weight:800;color:var(--ink);line-height:1.1;text-transform:uppercase;margin-bottom:5px}
  .title .acc{color:var(--blue)}
  .title.sm{font-size:7px;margin:4px 0 2px}
  .p{font-size:2.9px;line-height:1.45;margin-bottom:2.6px;text-align:justify}
  .sub{font-size:3.4px;font-weight:700;color:var(--blue);margin:2px 0 2px}
  .link{color:var(--blue)}
  ul.dots{list-style:none;margin:0 0 3px 6px}
  ul.dots li{font-size:2.9px;line-height:1.45;position:relative;padding-left:5px;margin-bottom:2px}
  ul.dots li::before{content:"";position:absolute;left:0;top:1.2px;width:1.3px;height:1.3px;border-radius:50%;background:var(--text)}

  /* cover */
  .cover-photo{position:absolute;left:0;top:0;width:212px;height:190px}
  .cover-title{position:absolute;left:14px;top:44px;font-family:"Oswald",sans-serif;color:#fff;line-height:.95}
  .cover-title .l1{font-size:13px;font-weight:500}
  .cover-title .l2{font-size:41px;font-weight:700;color:rgba(255,255,255,.45);letter-spacing:.5px}
  .cover-title .l3{font-size:27px;font-weight:600}
  .brand{position:absolute;left:0;right:0;top:212px;text-align:center;font-size:15px;font-weight:500;color:#3a3a3f;letter-spacing:1px}
  .brand .sq{display:inline-block;width:6px;height:6px;background:#3a3a3f;margin-right:4px;vertical-align:2px}
  .cover-pill{position:absolute;left:34px;right:34px;top:252px;height:22px;background:var(--blue);border-radius:8px;color:#fff;font-size:5.8px;font-weight:600;text-align:center;display:flex;flex-direction:column;justify-content:center;line-height:1.25}
  .cover-foot{position:absolute;left:0;right:0;top:282px;text-align:center;font-size:5.3px;font-weight:500;color:var(--ink)}
  .cover-foot b{color:var(--blue);font-weight:600}

  .tag{display:inline-block;background:var(--ink);color:#fff;font-size:4px;font-weight:600;padding:1.5px 4px;border-radius:4px;margin-bottom:5px;border:.6px solid #fff;outline:.6px solid var(--ink)}

  /* table of contents */
  .toc{list-style:none}
  .toc li{display:flex;align-items:baseline;font-size:2.7px;height:7.9px;line-height:7.9px}
  .toc .n{width:7px;color:#777}
  .toc .lb{font-weight:600;color:var(--ink);white-space:nowrap}
  .toc .lead{flex:1;border-bottom:.4px solid #999;margin:0 1px;transform:translateY(-1px)}
  .toc .pg{width:4px;text-align:right}
  .toc li.s .lb{color:var(--blue);font-weight:500;font-style:italic;padding-left:7px}

  /* contacts */
  .note{font-size:2.9px;font-weight:600;color:var(--ink);line-height:1.45;margin-bottom:5px}
  table.contacts{border-collapse:collapse;width:192px;font-size:2.4px}
  table.contacts td{height:4.85px;padding:0 2px;border:.3px solid #888;white-space:nowrap}
  table.contacts td.v{background:var(--blue);color:#fff;border-color:var(--blue);width:96px}
  table.contacts tr.hi td.k{background:var(--ink);color:#fff;font-weight:700}

  /* obligations */
  ol.rules{list-style:none;position:relative;padding-left:9px}
  ol.rules::before{content:"";position:absolute;left:2px;top:0;bottom:0;width:3px;background:var(--blue);border-radius:2px}
  ol.rules li{font-size:2.85px;line-height:1.45;margin-bottom:3.6px;position:relative;counter-increment:r}
  ol.rules li::before{content:counter(r) ".";position:absolute;left:-8.5px;color:#fff;font-size:2.4px;font-weight:700}
  .strong{font-size:3.2px;font-weight:800;color:var(--ink);margin-bottom:2px}
  .board{font-size:2.8px;line-height:1.5;margin-left:6px}
  .board div{display:grid;grid-template-columns:30px 46px 30px}

  .map{width:100px;height:70px;margin:0 0 8px 0;border:.8px solid var(--green)}
</style>
</head>
<body>
<div class="stage">
  <svg class="backdrop" width="1172" height="1200" viewBox="0 0 1172 1200" aria-hidden="true">
    <rect width="1172" height="1200" fill="#d6d7dc"/>
    <circle cx="1060" cy="430" r="560" fill="#b6bace"/>
    <polygon points="250,1200 720,1200 1172,760 1172,360" fill="#b6bace"/>
    <polygon points="0,640 300,380 560,380 0,900" fill="#c7c9d6"/>
    <circle cx="330" cy="1210" r="430" fill="#bcc0d3"/>
  </svg>

  <!-- Page: cover -->
  <section class="page c1 r1">
    <svg class="cover-photo" viewBox="0 0 212 190" role="img" aria-label="Aerial photo of the coastal resort town tinted in blue">
      <defs>
        <linearGradient id="coverTint" x1="0" y1="0" x2="1" y2="1">
          <stop offset="0" stop-color="#3c5cb6"/>
          <stop offset=".6" stop-color="#5f79c4"/>
          <stop offset="1" stop-color="#8799cf"/>
        </linearGradient>
      </defs>
      <path d="M0 0 H212 V100 C180 110 150 128 128 150 C110 168 85 170 60 160 C35 150 15 140 0 138 Z" fill="url(#coverTint)"/>
      <path d="M212 118 C185 118 160 132 150 150 C140 168 150 184 170 186 C190 188 205 180 212 176 Z" fill="#2a4ba8"/>
    </svg>
    <div class="cover-title">
      <div class="l1">VALE SERRA VILLAGE AND</div>
      <div class="l2">ORCHARD</div>
      <div class="l3">GARDENS</div>
    </div>
    <div class="brand"><span class="sq"></span>ORCHARD GARDENS</div>
    <div class="cover-pill"><span>VALE SERRA RESORT, 8100 – 000,</span><span>ALMADA NORTE, PORTUGAL</span></div>
    <div class="cover-foot">OWNERS HANDBOOK <b>2023</b></div>
  </section>

  <!-- Page: preface -->
  <section class="page c2 r1">
    <div class="run-head"><span class="tab"></span><span class="bar">VALE SERRA VILLAGE AND ORCHARD GARDENS</span></div>
    <div class="body">
      <h2 class="title"><span class="acc">Preface</span></h2>
      <span class="tag">OWNERS HANDBOOK – 2023</span>
      <p class="p">This handbook has been constructed and produced for the benefit of the Vale Serra Owners and has been produced by existing Owners who have volunteered their time and efforts in the Handbook's production.</p>
      <p class="p">If anything of note is missing or incorrect, then please let a Board member know and this will ensure the next version is improved.</p>
    </div>
    <div class="run-foot"><span>OWNERS HANDBOOK 2023</span><span>PAGE 01 of 12</span></div>
  </section>

  <!-- Page: table of contents -->
  <section class="page c3 r1">
    <div class="run-head"><span class="tab"></span><span class="bar">VALE SERRA VILLAGE AND ORCHARD GARDENS</span></div>
    <div class="body">
      <h2 class="title"><span class="acc">Table of</span> Contents</h2>
      <ul class="toc">
        <li><span class="n">01</span><span class="lb">PREFACE</span><span class="lead"></span><span class="pg">2</span></li>
        <li><span class="n">02</span><span class="lb">Useful Contacts</span><span class="lead"></span><span class="pg">4</span></li>
        <li><span class="n">03</span><span class="lb">Vale Serra Village and Orchard Gardens – Introduction</span><span class="lead"></span><span class="pg">5</span></li>
        <li><span class="n">04</span><span class="lb">Our Board</span><span class="lead"></span><span class="pg">5</span></li>
        <li><span class="n">05</span><span class="lb">Owners – Primary Obligations</span><span class="lead"></span><span class="pg">8</span></li>
        <li><span class="n">06</span><span class="lb">Valuable Information</span><span class="lead"></span><span class="pg">10</span></li>
        <li class="s"><span class="n"></span><span class="lb">01 Your Apartment</span><span class="lead"></span><span class="pg">10</span></li>
        <li class="s"><span class="n"></span><span class="lb">02 Our Rules and Regulations</span><span class="lead"></span><span class="pg">11</span></li>
        <li><span class="n">07</span><span class="lb">The Gardens Common Area – CLUB RULES</span><span class="lead"></span><span class="pg">12</span></li>
        <li><span class="n">08</span><span class="lb">TV and Internet Services</span><span class="lead"></span><span class="pg">13</span></li>
        <li><span class="n">09</span><span class="lb">Local Knowledge</span><span class="lead"></span><span class="pg">13</span></li>
        <li class="s"><span class="n"></span><span class="lb">01 Restaurants – Cafes – Shops</span><span class="lead"></span><span class="pg">14</span></li>
        <li class="s"><span class="n"></span><span class="lb">02 Communal WiFi</span><span class="lead"></span><span class="pg">15</span></li>
        <li class="s"><span class="n"></span><span class="lb">03 Waste Disposal</span><span class="lead"></span><span class="pg">15</span></li>
        <li class="s"><span class="n"></span><span class="lb">04 Cash Machines (ATM)</span><span class="lead"></span><span class="pg">15</span></li>
        <li class="s"><span class="n"></span><span class="lb">05 Air Conditioning</span><span class="lead"></span><span class="pg">15</span></li>
        <li class="s"><span class="n"></span><span class="lb">06 Electricity Supply</span><span class="lead"></span><span class="pg">15</span></li>
        <li class="s"><span class="n"></span><span class="lb">07 Apartment Alarms</span><span class="lead"></span><span class="pg">16</span></li>
        <li class="s"><span class="n"></span><span class="lb">08 Pool and Gardens Maintenance</span><span class="lead"></span><span class="pg">16</span></li>
        <li class="s"><span class="n"></span><span class="lb">09 Fire Safety</span><span class="lead"></span><span class="pg">16</span></li>
        <li class="s"><span class="n"></span><span class="lb">10 Public Transport</span><span class="lead"></span><span class="pg">16</span></li>
        <li><span class="n">10</span><span class="lb">Appendix 1 – PEAK SEASON PROCEDURES</span><span class="lead"></span><span class="pg">17</span></li>
        <li><span class="n">11</span><span class="lb">Appendix 2 – Fire Evacuation Procedures</span><span class="lead"></span><span class="pg">18</span></li>
      </ul>
    </div>
    <div class="run-foot"><span>OWNERS HANDBOOK 2023</span><span>PAGE 01 of 12</span></div>
  </section>

  <!-- Page: useful contacts -->
  <section class="page c4 r1">
    <div class="run-head"><span class="tab"></span><span class="bar">VALE SERRA VILLAGE AND ORCHARD GARDENS</span></div>
    <div class="body">
      <h2 class="title"><span class="acc">Useful</span> Contacts</h2>
      <p class="note">PLEASE NOTE THE SUFFIX CODE FOR ALL APART FROM THE EMERGENCY SERVICES IF NOT USING A PORTUGUESE MOBILE IS 00351 or +351</p>
      <table class="contacts">
        <tr><td class="k">POLICE – EMERGENCY</td><td class="v">112</td></tr>
        <tr><td class="k">FIRE BRIGADE</td><td class="v">112</td></tr>
        <tr><td class="k">AMBULANCE</td><td class="v">112</td></tr>
        <tr class="hi"><td class="k">EMERGENCY DOCTOR</td><td class="v">CALL SECURITY</td></tr>
        <tr><td class="k"></td><td class="v"></td></tr>
        <tr><td class="k">VALE SERRA CUSTOMER SERVICE</td><td class="v">200 000 101</td></tr>
        <tr><td class="k">CONDOMINIUM OFFICE (OFFICE HOURS)</td><td class="v">200 000 102</td></tr>
        <tr><td class="k">CONDOMINIUM (OUT OF HOURS EMERGENCY)</td><td class="v">900 000 103</td></tr>
        <tr class="hi"><td class="k">GUARD SEVEN SECURITY OFFICE</td><td class="v">200 000 104</td></tr>
        <tr class="hi"><td class="k">GUARD SEVEN MOBILE</td><td class="v">900 000 105</td></tr>
        <tr><td class="k">LOCAL POLICE (TOWN)</td><td class="v">200 000 106</td></tr>
        <tr><td class="k">LOCAL POLICE (VILLAGE)</td><td class="v">200 000 107</td></tr>
        <tr><td class="k">MEDICAL CENTRE</td><td class="v">200 000 108</td></tr>
        <tr><td class="k">CENTRAL CLINIC</td><td class="v">200 000 109</td></tr>
        <tr><td class="k">PHARMACY (MAIN ROAD)</td><td class="v">200 000 110</td></tr>
        <tr><td class="k">PHARMACY (TOWN)</td><td class="v">200 000 111</td></tr>
        <tr><td class="k">PHARMACY (VILLAGE)</td><td class="v">900 000 112</td></tr>
        <tr><td class="k">HOSPITAL (CITY)</td><td class="v">200 000 113</td></tr>
        <tr class="hi"><td class="k">HOSPITAL – NEAREST ONE</td><td class="v">200 000 114</td></tr>
        <tr><td class="k">24H ASSISTANCE (ELECTRIC COMPANY)</td><td class="v">800 000 115</td></tr>
        <tr><td class="k">GAS 24H ASSISTANCE</td><td class="v">800 000 116</td></tr>
        <tr><td class="k">GAS 24H ASSISTANCE (BOTTLED)</td><td class="v">200 000 117</td></tr>
        <tr><td class="k">AQUASERVA 24H ASSISTANCE (WATER)</td><td class="v">200 000 118</td></tr>
        <tr class="hi"><td class="k">TAXIS and LIMO SERVICE</td><td class="v">900 000 119 / 900 000 120</td></tr>
        <tr><td class="k"></td><td class="v">200 000 121</td></tr>
        <tr><td class="k">OTHER TAXIS</td><td class="v">200 000 122 / 200 000 123</td></tr>
        <tr><td class="k">AIRPORT</td><td class="v">200 000 124</td></tr>
        <tr><td class="k">BUS STATION</td><td class="v">200 000 125</td></tr>
        <tr><td class="k">TRAIN STATION</td><td class="v">200 000 126</td></tr>
        <tr><td class="k">LOCKSMITH (SAFE AND SECURE COMPANY)</td><td class="v">900 000 127</td></tr>
      </table>
    </div>
    <div class="run-foot"><span>OWNERS HANDBOOK 2023</span><span>PAGE 01 of 12</span></div>
  </section>

  <!-- Page: introduction & board -->
  <section class="page c1 r2">
    <div class="run-head"><span class="tab"></span><span class="bar">VALE SERRA VILLAGE AND ORCHARD GARDENS</span></div>
    <div class="body">
      <h2 class="title" style="margin-bottom:2px">Vale Serra Village and Orchard Gardens<br><span class="acc">Introduction</span></h2>
      <p class="p">The primary purpose of this Owners Handbook is to provide the Owners with valuable up to date information on all things Vale Serra Village and Gardens.</p>
      <p class="p">The Vale Serra Village development represents a five-phase property development of 194 apartments comprising a combination of two and three-bedroom units.</p>
      <p class="p">As Owners, we have made financial investments for our respective property and as Owners we also have obligations to ensure we all support the investments made by ensuring our property assets are not only protected but retain and enhance in value through the years.</p>
      <p class="p">Vale Serra Village and Orchard Gardens are quite unique compared to other condominium properties in the region and as such our uniqueness adds value to our investment. It's in all our interests to ensure we contribute to the continuing value enhancement of our village and gardens.</p>
      <p class="p">Throughout the years since the Condominium has existed, Owners have been the foundation of our success and without naming any individual Owners, many have contributed directly by taking responsibility for being on the Owners Board and in doing so they have given immense value to our overall resort well-being and success.</p>
      <p class="p">Board members provide many hours on behalf of all the Owners, for zero remuneration and as such they should be commended for their selfless commitments.</p>
      <p class="p">We do have a legal structure including Rules and Regulations for all aspects of the Condominium and these can be found in the separate Owners – Rules and Regulations publication.</p>
      <h3 class="title sm"><span class="acc">Our</span> Board</h3>
      <p class="p">Annually at the Owners General Meeting (held typically in Q1 of each year), Owners have the opportunity of being nominated and thereafter selected by the Owners voting for them to become an active member of the Owners Board.</p>
      <p class="p">Our selected Board Members have in recent years agreed voluntarily to perform their respective roles on the board for a 12-month term, without receiving any remuneration. A magnanimous commitment considering the hours that each Board Member allocates to the successful management and operation of the Complex.</p>
      <p class="p" style="font-weight:600;color:var(--ink)">Current (2022 – 2023) Board Members and respective contact details are as follows:</p>
      <div class="board">
        <div><span>• Tom Harlow</span><span>tom.harlow@example.com</span><span>+44 7000 000101</span></div>
        <div><span>• Jane Morrow</span><span>jane.m@example.com</span><span>+44 7000 000102</span></div>
        <div><span>• Elise Varda</span><span>elise.v@example.com</span><span>+32 400 00 0103</span></div>
        <div><span>• Rob Kelling</span><span>rob.k@example.com</span><span>+44 7000 000104</span></div>
      </div>
    </div>
    <div class="run-foot"><span>OWNERS HANDBOOK 2023</span><span>PAGE 01 of 12</span></div>
  </section>

  <!-- Page: primary obligations -->
  <section class="page c2 r2">
    <div class="run-head"><span class="tab"></span><span class="bar">VALE SERRA VILLAGE AND ORCHARD GARDENS</span></div>
    <div class="body">
      <h2 class="title" style="margin-bottom:10px"><span class="acc">Owners –</span> Primary Obligations</h2>
      <p class="strong">All Owners have equal OBLIGATIONS / COMMITMENT / RESPONSIBILITIES within our condominium complex.</p>
      <p class="sub">The following Owner Obligations are MANDATORY:</p>
      <ol class="rules">
        <li>To ensure the Property Management company is made aware immediately of any improvements identified or required.</li>
        <li>To always ensure ALL users of your apartment respect and adhere to the Rules and Regulations of the Condominium (refer to the separate Rules and Regulations document).</li>
        <li>To recognise the Owners elected Board as our primary representatives in relation to the successful operational running and financial management of the complex during their term in office.</li>
        <li>The area outside each property boundary is communal, therefore Owners are reminded not to place / fix any obstruction within the communal areas.</li>
        <li>To pay relevant Condominium Fees on time.</li>
        <li>To pay any Late Payment Fees / Fines in a prompt timeframe.</li>
        <li>To inform the local government financial authority that if a property is being used for commercial gain, through rental income or similar.</li>
        <li>To be mindful of your fellow owners and neighbours and ensure noise levels and behaviour are in keeping with our Rules and Regulations.</li>
        <li>To report to Security any / all suspicious incidents or behaviour unbecoming of the Rules of the Condominium.</li>
        <li>To report to Security any unruly behavior, at any time of the day but particularly after the 9pm threshold; that breaches our Peace and Tranquility rules.</li>
        <li>To report to the Property Management Company of any external repairs required on your property.</li>
        <li>To report to the Property Management Company anything that is broken or in need of repair within the Complex.</li>
        <li>Ensure the Central Area Gardens are always kept tidy, by placing all waste in the waste receptacles provided throughout the Gardens area.</li>
      </ol>
    </div>
    <div class="run-foot"><span>OWNERS HANDBOOK 2023</span><span>PAGE 01 of 12</span></div>
  </section>

  <!-- Page: TV, internet and local knowledge -->
  <section class="page c3 r2">
    <div class="run-head"><span class="tab"></span><span class="bar">VALE SERRA VILLAGE AND ORCHARD GARDENS</span></div>
    <div class="body">
      <h2 class="title" style="margin-bottom:9px"><span class="acc">TV and Internet</span> Services</h2>
      <p class="p">Included within your annual Condominium Fees is access to many TV channels delivered through the co-axial tv cable points within your Apartment. Should you experience any difficulties accessing the TV channels please contact Security.</p>
      <p class="p" style="margin-top:8px">Owners are free to use any of the many Internet service providers in Portugal, however your Board have negotiated a very good arrangement with a local renowned Internet provider called BrightLine Net.</p>
      <p class="p">BrightLine Net, as well as providing internet services directly to the Owners, they also have a contract with the Property Management company to maintain the co-axial TV services mentioned above. Their details can be found at <span class="link">www.brightline-net.example</span></p>
      <h3 class="title sm" style="margin-top:7px"><span class="acc">Local</span> Knowledge</h3>
      <p class="sub">Insurance</p>
      <ul class="dots">
        <li>Buildings Insurance is MANDATORY – IT IS included within the Condominium annual fees for those Owners who have requested to be included. OWNERS WHO HAVE OPTED OUT OF THIS ARRANGEMENT HAVE TO ORGANISE THEIR OWN BUILDINGS INSURANCE!</li>
        <li>Contents Insurance is the direct responsibility of every Apartment Owner, should you require this type of insurance.</li>
      </ul>
      <p class="sub" style="margin-top:5px">Harbour Living Company (Customer Services)</p>
      <p class="p">Customer Services for the Vale Serra resort is provided by Harbour Living. All post to your Apartment is delivered to Customer Services and not the boxes outside your Apartment.</p>
      <p class="p">Based within the office complex next to Anchor Pub, is the Harbour Living company. The Manager is assisted by a colleague also in the office. Full details can be found at <span class="link">www.harbourliving.example</span></p>
      <p class="p">Harbour Living provide a range of services to Owners including receiving mail, parcel deliveries, maintaining and cleaning properties and work with some of the Owners who rent out their property through them.</p>
      <p class="p">Harbour Living also provide property management services to individual owner.</p>
    </div>
    <div class="run-foot"><span>OWNERS HANDBOOK 2023</span><span>PAGE 01 of 12</span></div>
  </section>

  <!-- Page: valuable information -->
  <section class="page c4 r2">
    <div class="run-head"><span class="tab"></span><span class="bar">VALE SERRA VILLAGE AND ORCHARD GARDENS</span></div>
    <div class="body" style="top:26px">
      <h2 class="title" style="margin-bottom:1px"><span class="acc">Cash Machines</span> (ATM)</h2>
      <p class="p">There are 2 ATM machines in our area, one is beside Anchor pub and the other one in between the Bistro and the Supermarket.</p>
      <h2 class="title" style="margin:4px 0 1px"><span class="acc">Air</span> Conditioning</h2>
      <p class="p">The majority if not all the Apartments are using A/C within the apartment. It is advisable to have your respective A/C units and chiller serviced on a regular basis. There are quite a few local A/C maintenance service providers, including:</p>
      <ul class="dots" style="margin-top:3px">
        <li>CoolAir Lda – +351 200 000 131</li>
        <li>FrostLine – +351 200 000 132</li>
      </ul>
      <h2 class="title" style="margin:4px 0 1px"><span class="acc">Electricity</span> Supply</h2>
      <p class="p">In many parts of the region, intermittent and disrupted electrical supply can occur, this may require in some instances for the Owner to call Security. Access to the Services cupboard on the ground floor in each block (where the individual electricity meters are located) is through the key provided to each apartment or alternatively by contacting Security who can open the services doors.</p>
      <h2 class="title" style="margin:6px 0 1px"><span class="acc">Apartment</span> Alarms</h2>
      <p class="p">A number of apartments have alarms connected to the Guard Seven security centre situated in the security office opposite the Ember restaurant and near to B0 block.</p>
      <p class="p">If you are leaving your apartment for any period of time, we strongly recommend you advise the Property Management company – Customer Services and advise them if your alarm is on.</p>
      <h2 class="title" style="margin:6px 0 1px"><span class="acc">Pool and Gardens</span> Maintenance</h2>
      <p class="p">The Gardens and Pool maintenance is outsourced to a local company who are responsible for the upkeep of every aspect of the Gardens and Pools and similarly in all common areas surrounding and attached to our complex.</p>
      <p class="p">Throughout the year you will hear and see the gardening or Pool staff at work, keeping our Gardens beautiful.</p>
      <p class="sub" style="font-size:2.9px">PEST CONTROL</p>
      <p class="p" style="color:var(--blue);font-weight:600">We have continual Pest Control programme in place and in particular for dealing with the processionary caterpillars that become evident in the early spring of each year. If you see a procession near your apartment block or in the Gardens area, PLEASE ALERT THE PROPERTY MANAGEMENT COMPANY ASAP!</p>
    </div>
    <div class="run-foot"><span>OWNERS HANDBOOK 2023</span><span>PAGE 01 of 12</span></div>
  </section>

  <!-- Page: TV and internet (detailed) -->
  <section class="page c1 r3">
    <div class="run-head"><span class="tab"></span><span class="bar">VALE SERRA VILLAGE AND ORCHARD GARDENS</span></div>
    <div class="body" style="top:40px">
      <h2 class="title" style="margin-bottom:3px"><span class="acc">TV and Internet</span> Services</h2>
      <p class="sub">TV</p>
      <p class="p">Included within your annual Condominium Fees is access to many TV channels delivered through the co-axial tv cable points within your Apartment. Should you experience any difficulties accessing the TV channels please contact Security.</p>
      <p class="sub" style="margin-top:4px">Internet</p>
      <p class="p">Owners are free to use any of the many Internet service providers in Portugal, however your Board have negotiated a very good arrangement with a local renowned Internet provider called BrightLine Net.</p>
      <p class="p">BrightLine Net, as well as providing internet services directly to the Owners, they also have a contract with the Property Management company to maintain the co-axial TV services mentioned above. Their details can be found at <span class="link">www.brightline-net.example</span></p>
      <h3 class="title sm" style="margin-top:7px"><span class="acc">Local</span> Knowledge</h3>
      <p class="sub">Insurance</p>
      <ul class="dots">
        <li>Buildings Insurance is MANDATORY – IT IS included within the Condominium annual fees for those Owners who have requested to be included. OWNERS WHO HAVE OPTED OUT OF THIS ARRANGEMENT HAVE TO ORGANISE THEIR OWN BUILDINGS INSURANCE!</li>
        <li>Contents Insurance is the direct responsibility of every Apartment Owner, should you require this type of insurance.</li>
      </ul>
      <p class="sub" style="margin-top:4px">Harbour Living Company (Customer Services)</p>
      <p class="p">Customer Services for the Vale Serra resort is provided by Harbour Living. All post to your Apartment is delivered to Customer Services and not the boxes outside your Apartment.</p>
      <p class="p">Based within the office complex next to Anchor pub, is the Harbour Living company. The Manager is assisted by a colleague also in the office. Full details can be found at <span class="link">www.harbourliving.example</span></p>
      <p class="p">Harbour Living provide a range of services to Owners including receiving mail, parcel deliveries, maintaining and cleaning properties and work with some of the Owners who rent out their property through them.</p>
      <p class="p">Harbour Living also provide property management services to individual owner.</p>
    </div>
    <div class="run-foot"><span>OWNERS HANDBOOK 2023</span><span>PAGE 01 of 12</span></div>
  </section>

  <!-- Page: restaurants, cafes, shops -->
  <section class="page c2 r3">
    <div class="run-head"><span class="tab"></span><span class="bar">VALE SERRA VILLAGE AND ORCHARD GARDENS</span></div>
    <div class="body" style="top:33px">
      <h2 class="title" style="margin-bottom:4px"><span class="acc">Restaurants</span> – Cafes – Shops</h2>
      <div class="board" style="margin-left:0;font-size:2.6px;line-height:3.3">
        <div style="grid-template-columns:36px 140px"><b>Anchor Pub</b><span>+351 200 000 141 (dine in and takeaway service available)</span></div>
        <div style="grid-template-columns:36px 140px"><b>Cork Bistro</b><span>+351 900 000 142</span></div>
        <div style="grid-template-columns:36px 140px"><b>Ember Steakhouse</b><span>+351 200 000 143</span></div>
      </div>
      <h3 class="title sm" style="margin-top:2px"><span class="acc">Café's within the Resort</span></h3>
      <div class="board" style="margin-left:0;font-size:2.6px">
        <div style="grid-template-columns:30px 150px"><span>1. Serra Café</span><span>+351 900 000 144 (dine in and takeaway service available)</span></div>
        <div style="grid-template-columns:30px 150px"><span>2. Café da Praça</span><span>+351 900 000 145 (dine in and takeaway service available)</span></div>
      </div>
      <h3 class="title sm"><span class="acc">Supermarket</span></h3>
      <p class="p">We have a small supermarket Mercadinho Sol within the resort (next to the Serra Café)</p>
      <h3 class="title sm"><span class="acc">Hairdressers</span></h3>
      <p class="sub" style="font-size:2.6px;margin-top:0">WITHIN THE COMPLEX:</p>
      <div class="board" style="font-size:2.6px">
        <div style="grid-template-columns:34px 60px"><span>• Hair and Beauty Salon</span><span>+351 900 000 146</span></div>
        <div style="grid-template-columns:34px 60px"><span>• Studio Salon</span><span>+351 900 000 147</span></div>
      </div>
      <h3 class="title sm" style="margin-top:6px"><span class="acc">Serrano Hotel and Golf Course</span></h3>
      <p class="p">A short drive and not too far walk away is the Serrano Hotel and Golf club.</p>
      <p class="p">Vale Serra Owners receive a discount for golf at the club and please ensure you show the reception desk your Owners card with up-to-date year label on the card. Please note the Owners card is available from Customer Service Offices at Harbour Living office (beside Anchor Pub).</p>
      <h3 class="title sm" style="margin-top:1px"><span class="acc">Communal WiFi</span></h3>
      <p class="p">A communal WiFi service is provided in the Gardens Area next to the main pool Area for all Owners and their guest to use.</p>
      <p class="p">Username and Passwords are updated regularly, and full details can be obtained from staff working in the Bar area of the Gardens.</p>
      <h3 class="title sm" style="margin-top:1px"><span class="acc">Waste Disposal</span></h3>
      <p class="p">Owners are responsible for the proper use of the Condominium waste disposal bins strategically placed near each apartment block by the Waste disposal company AquaServa.</p>
      <p class="p">Please remember to ensure you separate Plastics and glass from the general waste you are disposing.</p>
    </div>
    <div class="run-foot"><span>OWNERS HANDBOOK 2023</span><span>PAGE 01 of 12</span></div>
  </section>

  <!-- Page: fire safety & transport -->
  <section class="page c3 r3">
    <div class="run-head"><span class="tab"></span><span class="bar">VALE SERRA VILLAGE AND ORCHARD GARDENS</span></div>
    <div class="body" style="top:33px">
      <h2 class="title" style="margin-bottom:3px"><span class="acc">Fire</span> Safety</h2>
      <p class="p" style="color:var(--blue);font-weight:700;font-style:italic">SHOULD YOU DETECT A FIRE IN YOUR APARTMENT, BLOCK, COMMON AREAS OR GARDENS ALERT SECURITY AND PLEASE CALL 112 FOR THE FIRE BRIGADE WHO WILL ARRIVE TO DEAL WITH THE ISSUE.</p>
      <p class="p" style="font-weight:700;color:var(--ink);margin-top:4px">FULL FIRE EVACUATION PROCEDURES ARE CONTAINED WITHIN APPENDIX 2 OF THIS HANDBOOK</p>
      <h2 class="title" style="margin:8px 0 3px"><span class="acc">Public</span> Transport</h2>
      <p class="p">Public buses run on the main road adjoining the entrance to Vale Serra, bus stops are on both sides of the main road (the main road outside the complex).</p>
      <p class="p" style="margin-top:4px">Trains are available and nearest stations are at the city, the town and the village.</p>
    </div>
    <div class="run-foot"><span>OWNERS HANDBOOK 2023</span><span>PAGE 01 of 12</span></div>
  </section>

  <!-- Page: appendix 2 -->
  <section class="page c4 r3">
    <div class="run-head"><span class="tab"></span><span class="bar">VALE SERRA VILLAGE AND ORCHARD GARDENS</span></div>
    <div class="body" style="top:33px">
      <h2 class="title" style="margin-bottom:7px"><span class="acc">Appendix 2</span><br>Fire Evacuation Procedures</h2>
      <svg class="map" viewBox="0 0 100 70" role="img" aria-label="Emergency evacuation floor plan with exit routes and safety instructions">
        <rect width="100" height="70" fill="#f3f6f3"/>
        <rect width="100" height="4" fill="#2e9a49"/>
        <rect y="46" width="100" height="2" fill="#2e9a49"/>
        <rect y="48" width="100" height="22" fill="#e3efe6"/>
      </svg>
      <svg class="map" viewBox="0 0 100 70" role="img" aria-label="Second emergency evacuation floor plan with exit routes and safety instructions">
        <rect width="100" height="70" fill="#f3f6f3"/>
        <rect width="100" height="4" fill="#2e9a49"/>
        <rect y="46" width="100" height="2" fill="#2e9a49"/>
        <rect y="48" width="100" height="22" fill="#e3efe6"/>
      </svg>
    </div>
    <div class="run-foot"><span>OWNERS HANDBOOK 2023</span><span>PAGE 01 of 12</span></div>
  </section>
</div>
</body>
</html>
```